Business card design for Automotive workshop

We need a business card for a new automotive repair and tyre shop called Keelstone Prime Automotive located in New Zealand. We are a clean, modern and fresh workshop and company.

Front needs to feature logo,
my name:
Marlo Fenwicke (director)

Address:
48 Tarn Lane
Harrowby 3592

Phone: 07 594 2713
Mobile: 027 451 9362
Email: office@keelstoneautomotive.example.nz
Website: keelstoneautomotive.example.nz

Back needs to feature an area to write down appointment details, date and time.

Also feature a list of jobs and work we do such as,
Vehicle Servicing
All Mechanical Repairs
Warrant of Fitness
Tyres & Wheel Alignments
Automotive Diagnostics
Automotive Parts & Supplies

```html
<!DOCTYPE html>
<html lang="en">
<head>
<meta charset="utf-8">
<title>Keelstone Prime Automotive – Business Card</title>
<link href="https://fonts.googleapis.com/css2?family=Lato:wght@400;700;900&display=swap" rel="stylesheet">
<style>
  :root {
    --stage: #262626;
    --charcoal: #3c3c3d;
    --red: #e01d2b;
    --ink: #2b2b2b;
    --muted: #555555;
    --paper: #ffffff;
    --rule: #9a9a9a;
  }
  * { box-sizing: border-box; margin: 0; padding: 0; }
  html, body { width: 1200px; height: 852px; overflow: hidden; }
  body {
    background: var(--stage);
    font-family: "Lato", sans-serif;
    display: flex; align-items: center; justify-content: center; gap: 40px;
  }
  .card {
    width: 540px; height: 309px; background: var(--paper);
    position: relative; overflow: hidden;
    box-shadow: 0 10px 30px rgba(0,0,0,.45);
  }

  /* Back */
  .card-back__top {
    height: 186px; background: var(--charcoal);
    border-bottom: 3px solid var(--red);
    display: flex; flex-direction: column; align-items: center; justify-content: center; gap: 18px;
  }
  .brand-name {
    font-weight: 900; color: var(--red); text-transform: uppercase;
    letter-spacing: .02em; line-height: 1.05;
  }
  .card-back .brand-name { font-size: 26px; text-align: center; }
  .services { color: #f2f2f2; font-size: 13px; text-align: center; line-height: 1.55; }
  .services .sep { color: var(--red); padding: 0 6px; }
  .appointment { padding: 16px 40px 0; }
  .appointment__title { color: var(--red); font-size: 14px; text-align: center; margin-bottom: 22px; }
  .appointment__fields { display: flex; gap: 16px; font-size: 14px; color: var(--muted); }
  .field { display: flex; align-items: flex-end; gap: 6px; }
  .field--date { flex: 1.2; }
  .field--time { flex: 1; }
  .field__line { flex: 1; border-bottom: 1px solid var(--rule); height: 14px; }

  /* Front */
  .card-front .brand {
    position: absolute; left: 34px; top: 40px; display: flex; align-items: center; gap: 12px;
  }
  .brand-mark { width: 18px; height: 18px; background: var(--red); border-radius: 50%; flex: none; }
  .card-front .brand-name { font-size: 34px; }
  .person { position: absolute; right: 40px; top: 150px; text-align: right; }
  .person__name { color: var(--red); font-size: 26px; font-weight: 700; }
  .person__role { color: var(--muted); font-size: 14px; margin-top: 2px; }
  .divider { position: absolute; left: 34px; right: 34px; top: 222px; border-top: 1.5px solid var(--red); }
  .contacts {
    position: absolute; left: 34px; right: 34px; top: 236px;
    display: flex; justify-content: space-between; font-size: 12.5px; color: var(--ink); line-height: 1.6;
  }
  .contact-row { display: flex; align-items: center; gap: 6px; white-space: nowrap; }
  .contact-row svg { width: 11px; height: 11px; fill: var(--red); flex: none; }
  .address { display: flex; gap: 6px; white-space: nowrap; }
  .address svg { width: 11px; height: 14px; fill: var(--red); margin-top: 3px; flex: none; }
</style>
</head>
<body>

  <section class="card card-back" aria-label="Card back">
    <div class="card-back__top">
      <div class="brand-name">Keelstone Prime<br>Automotive</div>
      <div class="services">
        <div>Vehicle Servicing<span class="sep">|</span>All Mechanical Repairs</div>
        <div>Warrant of Fitness<span class="sep">|</span>Tyres &amp; Wheel Alignments</div>
        <div>Automotive Diagnostics<span class="sep">|</span>Automotive Parts &amp; Supplies</div>
      </div>
    </div>
    <div class="appointment">
      <div class="appointment__title">Appointment</div>
      <div class="appointment__fields">
        <div class="field field--date">Date <span class="field__line"></span></div>
        <div class="field field--time">Time <span class="field__line"></span></div>
      </div>
    </div>
  </section>

  <section class="card card-front" aria-label="Card front">
    <div class="brand">
      <span class="brand-mark"></span>
      <div class="brand-name">Keelstone Prime<br>Automotive</div>
    </div>
    <div class="person">
      <div class="person__name">Marlo Fenwicke</div>
      <div class="person__role">Director</div>
    </div>
    <div class="divider"></div>
    <div class="contacts">
      <div>
        <div class="contact-row"><svg viewBox="0 0 24 24"><path d="M6.6 10.8a15 15 0 0 0 6.6 6.6l2.2-2.2a1 1 0 0 1 1-.25 11.4 11.4 0 0 0 3.6.57 1 1 0 0 1 1 1V20a1 1 0 0 1-1 1A17 17 0 0 1 3 4a1 1 0 0 1 1-1h3.5a1 1 0 0 1 1 1c0 1.25.2 2.45.57 3.57a1 1 0 0 1-.25 1z"/></svg>07 594 2713</div>
        <div class="contact-row"><svg viewBox="0 0 24 24"><path d="M7 1h10a2 2 0 0 1 2 2v18a2 2 0 0 1-2 2H7a2 2 0 0 1-2-2V3a2 2 0 0 1 2-2zm0 4v13h10V5zm5 14.5a1 1 0 1 0 0 2 1 1 0 0 0 0-2z"/></svg>027 451 9362</div>
      </div>
      <div>
        <div class="contact-row"><svg viewBox="0 0 24 24"><path d="M2 5h20v14H2zm2 2v.5l8 5 8-5V7zm0 2.8V17h16V9.8l-8 5z"/></svg>office@keelstoneautomotive.example.nz</div>
        <div class="contact-row"><svg viewBox="0 0 24 24"><path d="M12 2a10 10 0 1 0 0 20 10 10 0 0 0 0-20zm6.9 6h-3a15 15 0 0 0-1.3-3.9A8 8 0 0 1 18.9 8zM12 4c.8 1.2 1.5 2.5 1.9 4h-3.8c.4-1.5 1.1-2.8 1.9-4zM4.3 14a8 8 0 0 1 0-4h3.4a16 16 0 0 0 0 4zm.8 2h3a15 15 0 0 0 1.3 3.9A8 8 0 0 1 5.1 16zm3-8h-3a8 8 0 0 1 4.3-3.9A15 15 0 0 0 8.1 8zM12 20c-.8-1.2-1.5-2.5-1.9-4h3.8c-.4 1.5-1.1 2.8-1.9 4zm2.3-6H9.7a14 14 0 0 1 0-4h4.6a14 14 0 0 1 0 4zm.3 5.9a15 15 0 0 0 1.3-3.9h3a8 8 0 0 1-4.3 3.9zm1.7-5.9a16 16 0 0 0 0-4h3.4a8 8 0 0 1 0 4z"/></svg>keelstoneautomotive.example.nz</div>
      </div>
      <div class="address">
        <svg viewBox="0 0 24 30"><path d="M12 0a11 11 0 0 0-11 11c0 8 11 19 11 19s11-11 11-19A11 11 0 0 0 12 0zm0 15a4 4 0 1 1 0-8 4 4 0 0 1 0 8z"/></svg>
        <div>48 Tarn Lane<br>Harrowby 3592</div>
      </div>
    </div>
  </section>

</body>
</html>
```